Holzdesign Firma sucht stilvolles Corporate Design
Zielgruppe
Ich stelle Utensilien aus Holz für die Küche her und verkaufe diese übers Internet. In erster Linie platzsparende Messerbretter aus Holz. Meine Zielgruppe ist jeder in Deutschland der eine Küche hat und dort kocht.
Aufgabenstellung
Das Design sollte eher schlicht und innovativ wirken. Der Name FELSGART muss mit ihm Logo sein. Im Logo sollte auch eine Verbindung zum Holz erkennbar sein, am besten mit einem Holzbalken oder einem Baumstamm. Im Logo sollen keine Weihnachtsbäume oder ganze Bäume sichtbar sein. Die Farbwahl würde ich auf Farben die zu Holz und Natur passen eingrenzen.
Mit dem Design will ich mich von den übrigen Handwerksbetrieben abheben und nicht einfach die üblichen Standarddesigns kopieren.

```html
<!DOCTYPE html>
<html lang="de">
<head>
<meta charset="utf-8">
<title>FELSGART – Corporate Design</title>
<link href="https://fonts.googleapis.com/css2?family=Barlow:wght@300;400;500;700;800&display=swap" rel="stylesheet">
<style>
  :root {
    --brown: #3d2316;
    --tan: #d4b084;
    --tan-text: #c9a06e;
    --paper: #ffffff;
    --bg-top: #f7f7f7;
    --bg-bottom: #e9e9e9;
    --label: #7a7a7a;
    --window: #ababab;
  }
  * { margin: 0; padding: 0; box-sizing: border-box; }
  html, body { width: 1200px; height: 801px; overflow: hidden; }
  body {
    position: relative;
    font-family: "Barlow", sans-serif;
    background: linear-gradient(180deg, var(--bg-top), var(--bg-bottom));
    color: var(--brown);
  }
  .abs { position: absolute; }

  /* brand wordmark */
  .brand {
    position: absolute;
    display: flex; align-items: center;
    transform: translate(-50%, -50%);
    white-space: nowrap;
  }
  .brand__dot {
    width: 0.55em; height: 0.55em; border-radius: 50%;
    background: var(--tan); margin-right: 0.25em; flex: none;
  }
  .brand__text { display: flex; flex-direction: column; line-height: 1; }
  .brand__name { font-weight: 800; letter-spacing: 0.04em; color: var(--brown); }
  .brand__slogan { font-weight: 400; font-size: 0.27em; color: var(--tan-text); margin-top: 0.35em; letter-spacing: 0.02em; }

  .brand--hero { left: 336px; top: 140px; font-size: 46px; }
  .brand--card { left: 188px; top: 375px; font-size: 24px; }
  .brand--envelope { left: 204px; top: 553px; font-size: 17px; }
  .brand--letter { left: 891px; top: 104px; font-size: 18px; }

  .view-label {
    position: absolute; top: 264px; font-size: 15.5px; font-weight: 300;
    color: var(--label); transform: translateX(-50%);
  }

  .sheet { position: absolute; background: var(--paper); box-shadow: 0 4px 10px rgba(0,0,0,0.18); }
  .card-front { left: 58px; top: 292px; width: 259px; height: 167px; }
  .card-back { left: 333px; top: 293px; width: 260px; height: 168px; }
  .envelope { left: 58px; top: 496px; width: 537px; height: 267px; }
  .letter { left: 630px; top: 34px; width: 521px; height: 737px; }

  .card-back__name { left: 35px; top: 84px; font-size: 12px; font-weight: 800; letter-spacing: 0.06em; }
  .card-back__band { left: 0; top: 101px; width: 100%; height: 4px; background: var(--brown); }
  .card-back__contact { left: 35px; top: 122px; font-size: 8.4px; line-height: 13px; color: var(--tan-text); letter-spacing: 0.02em; }

  .envelope__window { left: 47px; top: 121px; width: 206px; height: 111px; border-radius: 10px;
    background: linear-gradient(135deg, #bdbdbd, #a3a3a3); }

  .letter { font-size: 6.9px; line-height: 10.5px; color: #2a1a12; }
  .letter__sender { left: 63px; top: 160px; font-size: 5.5px; }
  .letter__sender b { font-weight: 700; }
  .letter__recipient { left: 63px; top: 174px; line-height: 12.2px; }
  .letter__contact { right: 32px; top: 136px; text-align: right; font-size: 6.3px; line-height: 10.4px; color: var(--tan-text); }
  .letter__contact .name { color: var(--brown); font-weight: 700; }
  .letter__contact p + p { margin-top: 7px; }
  .letter__subject { left: 63px; top: 244px; }
  .letter__body { left: 63px; top: 276px; width: 440px; }
  .letter__body p { margin-bottom: 10.5px; }
  .fold { left: 0; height: 1px; background: var(--tan); }
  .letter__band { left: 0; top: 655px; width: 100%; height: 12px; background: var(--brown); }
  .letter__footer { top: 690px; font-size: 6.3px; line-height: 10.4px; }
  .letter__footer b { font-weight: 700; }
</style>
</head>
<body>

  <div class="brand brand--hero">
    <span class="brand__dot"></span>
    <span class="brand__text"><span class="brand__name">FELSGART</span><span class="brand__slogan">Hier könnte Ihr Slogan stehen.</span></span>
  </div>

  <div class="view-label" style="left:187px">Visitenkarte vorne</div>
  <div class="view-label" style="left:462px">Visitenkarte hinten</div>

  <div class="sheet card-front"></div>
  <div class="brand brand--card">
    <span class="brand__dot"></span>
    <span class="brand__text"><span class="brand__name">FELSGART</span><span class="brand__slogan">Hier könnte Ihr Slogan stehen.</span></span>
  </div>

  <div class="sheet card-back">
    <div class="abs card-back__name">MAX MUSTERMANN</div>
    <div class="abs card-back__band"></div>
    <div class="abs card-back__contact">
      Musterstr. 5 | 45868 Muster | Tel.: 0341 772906<br>
      m.mustermann@felsgart.de | www.felsgart.de
    </div>
  </div>

  <div class="sheet envelope">
    <div class="abs envelope__window"></div>
  </div>
  <div class="brand brand--envelope">
    <span class="brand__dot"></span>
    <span class="brand__text"><span class="brand__name">FELSGART</span><span class="brand__slogan">Hier könnte Ihr Slogan stehen.</span></span>
  </div>

  <div class="sheet letter">
    <div class="abs fold" style="top:261px;width:12px"></div>
    <div class="abs fold" style="top:369px;width:24px"></div>
    <div class="abs fold" style="top:521px;width:12px"></div>

    <div class="abs letter__sender"><b>FELSGART</b> | Musterstraße 9 | 45868 Muster</div>
    <div class="abs letter__recipient">Herr Mustermann<br>Musterstraße 3<br>48555 Muster</div>

    <div class="abs letter__contact">
      <p><span class="name">FELSGART</span><br>Musterstraße 93a<br>55555 Muster</p>
      <p>Tel.: 0341 772906<br>Fax: 0341 772907<br>Mobil: 0176 4158230</p>
      <p>info@felsgart.de<br>www.felsgart.de</p>
    </div>

    <div class="abs letter__subject">Hier steht eine Betreffzeile</div>

    <div class="abs letter__body">
      <p>Sehr geehrte Frau Musterbeispiel,</p>
      <p>als Kunde unseres jungen und modernen Unternehmens erwartet<br>Sie Qualität in höchstem Maße.</p>
      <p>Sie können sicher zu sein, genau zu bekommen, was wir Ihnen versprechen.<br>Und damit werden Sie auch rundum zufrieden sein. Das garantieren wir Ihnen.</p>
      <p>Schauen Sie doch gleich das beiliegende Prospekt. Wir bieten Ihnen moderne und hochwertige Produkte, die auf dem neuesten Stand der Technik sind, an. Überzeugen Sie sich selbst von der hochwertigen Qualität unserer Produkte und bestellen Sie noch heute.</p>
      <p>Wir freuen uns auf Ihre Bestellung und sind bei Rückfragen gerne für Sie da.</p>
      <p>Mit freundlichen Grüßen</p>
    </div>

    <div class="abs letter__band"></div>
    <div class="abs letter__footer" style="left:50px"><b>FELSGART</b><br>Musterstraße 9<br>45868 Muster</div>
    <div class="abs letter__footer" style="left:189px">USt-IDNR: DE4726519<br>Steuernummer: 214/587/103<br>Inhaber: Max Mustermann</div>
    <div class="abs letter__footer" style="left:365px">Sparkasse Musterstadt<br>IBAN: DE41 2706 0000 0000 3385<br>BIC: FRANDEXX41</div>
  </div>
  <div class="brand brand--letter">
    <span class="brand__dot"></span>
    <span class="brand__text"><span class="brand__name">FELSGART</span><span class="brand__slogan">Hier könnte Ihr Slogan stehen.</span></span>
  </div>

</body>
</html>
```